business card

Business card for new business.
Red and black corporate colors.
Card can have an Indsutrial feel to it. Feel free to add Rust, Bolted steel, or graphics as you see fit. We provide highly specialized services to the below mentioned industries.
Keep information out of corners so that if I want I can choose rounded corners.
Information
- front. name - title - phone - email
- Rear
Forging - Marine - Pipelines - Quarrying - Utilities
Harlow Bay - Pine Ridge - North Alder - Stonebrook - Westmere

```html
<!DOCTYPE html>
<html lang="en">
<head>
<meta charset="utf-8">
<title>Ironstead business card</title>
<link rel="stylesheet" href="https://fonts.googleapis.com/css2?family=Roboto:wght@400;500&family=Roboto+Condensed:wght@500;700&display=swap">
<style>
  :root {
    --backdrop: #5a4939;
    --card-dark: #1c1d1f;
    --card-grey: #808080;
    --band-grey: #7d7d7d;
    --brand-red: #e3001b;
    --mark-grey: #8c8c8c;
    --title-grey: #7a7a7a;
    --white: #ffffff;
  }
  * { margin: 0; padding: 0; box-sizing: border-box; }
  html, body { width: 1200px; height: 960px; overflow: hidden; }
  body {
    position: relative;
    background: var(--backdrop);
    font-family: "Roboto", Arial, sans-serif;
  }
  .card {
    position: absolute;
    width: 600px;
    height: 343px;
    overflow: hidden;
  }
  .card-front { left: 314px; top: 113px; background: var(--card-dark); }
  .card-back { left: 311px; top: 472px; background: var(--card-grey); }

  .front-wordmark {
    position: absolute;
    top: 110px; left: 0; width: 100%;
    text-align: center;
    font-family: "Roboto Condensed", "Arial Narrow", sans-serif;
    font-weight: 700;
    font-size: 46px;
    letter-spacing: 1px;
    color: var(--mark-grey);
    line-height: 56px;
  }
  .person-name {
    position: absolute;
    top: 193px; left: 0; width: 100%;
    text-align: center;
    font-family: "Roboto Condensed", "Arial Narrow", sans-serif;
    font-weight: 500;
    font-size: 23px;
    color: var(--brand-red);
    text-transform: uppercase;
  }
  .person-title {
    position: absolute;
    top: 222px; left: 0; width: 100%;
    text-align: center;
    font-weight: 500;
    font-size: 14px;
    color: var(--title-grey);
    text-transform: uppercase;
  }
  .contact-band {
    position: absolute;
    left: 0; bottom: 0;
    width: 100%; height: 51px;
    background: var(--band-grey);
    border-top: 5px solid var(--brand-red);
  }
  .contact-item {
    position: absolute;
    top: 15px;
    transform: translateX(-50%);
    color: var(--white);
    font-size: 15px;
    white-space: nowrap;
  }
  .contact-icon {
    position: absolute;
    top: -21px;
    transform: translateX(-50%);
    width: 28px; height: 28px;
    border-radius: 50%;
    background: var(--card-dark);
    display: flex; align-items: center; justify-content: center;
  }
  .contact-icon svg { width: 12px; height: 12px; fill: var(--brand-red); }

  .back-wordmark {
    position: absolute;
    top: 118px; left: 0; width: 100%;
    text-align: center;
    font-family: "Roboto Condensed", "Arial Narrow", sans-serif;
    font-weight: 700;
    font-size: 56px;
    letter-spacing: 1px;
    color: var(--white);
    line-height: 64px;
  }
  .service-list {
    position: absolute;
    top: 257px; left: 0; width: 100%;
    text-align: center;
    color: var(--white);
    font-size: 15px;
    line-height: 18px;
  }
</style>
</head>
<body>
  <section class="card card-front">
    <div class="front-wordmark">IRONSTEAD</div>
    <div class="person-name">Daniel Hartwell</div>
    <div class="person-title">CEO/Founder</div>
    <div class="contact-band">
      <span class="contact-icon" style="left:113px">
        <svg viewBox="0 0 24 24"><path d="M6.6 10.8a15.1 15.1 0 0 0 6.6 6.6l2.2-2.2a1 1 0 0 1 1-.25 11.4 11.4 0 0 0 3.6.57 1 1 0 0 1 1 1V20a1 1 0 0 1-1 1A17 17 0 0 1 3 4a1 1 0 0 1 1-1h3.5a1 1 0 0 1 1 1c0 1.25.2 2.45.57 3.57a1 1 0 0 1-.25 1z"/></svg>
      </span>
      <span class="contact-item" style="left:116px">604 555 0182</span>
      <span class="contact-icon" style="left:278px">
        <svg viewBox="0 0 24 24"><path d="M2 5h20v14H2z"/><path d="M3 6l9 6.3L21 6v1.5l-9 6.3-9-6.3z" fill="#1c1d1f"/></svg>
      </span>
      <span class="contact-item" style="left:281px">info@ironstead.com</span>
      <span class="contact-icon" style="left:462px">
        <svg viewBox="0 0 24 24"><circle cx="12" cy="12" r="10"/><path d="M7 8c2 0 3 1 3 3s-2 2-2 4l-2 1M14 5c0 2 2 2 3 3s-1 3 1 4l2 0M13 16c1-1 3-1 3 1s-1 3-2 3" stroke="#1c1d1f" stroke-width="1.6" fill="none"/></svg>
      </span>
      <span class="contact-item" style="left:462px">www.ironstead.com</span>
    </div>
  </section>

  <section class="card card-back">
    <div class="back-wordmark">IRONSTEAD</div>
    <p class="service-list">
      Forging • Marine • Pipelines • Quarrying<br>
      Utilities • Harlow Bay • Pine Ridge • North Alder<br>
      Stonebrook • Westmere
    </p>
  </section>
</body>
</html>
```